Academic and Business book cover

I need a book cover for my academic and business book.
The focus is in international / global negotiation and influence (how to negotiate across cultures).
The book will be published on Zelvorn, both in Vaspet and printed edition. therefore I need something that works under Zelvorn guidelines.The final design should be elegant and still be able to stand out against the competition.
I would like to have orange+grey for the text colors on the cover, even if different options are welcome.
Title and my name are in the attached word doc.

Target Market(s)

graduates, Phds, from international business schools. Managers

Industry/Entity Type

Business

Font styles to use
Serif
Sans Serif

Colors

Designer to choose colors to be used in the design.

Requirements
Must have
• The title and my name should have elegant fonts.
Nice to have
• pictures of the world that don't have the "usual" Europe in the centre.

```html
<!DOCTYPE html>
<html lang="en">
<head>
<meta charset="utf-8">
<title>The 4Cs Compass — Book Cover</title>
<link href="https://fonts.googleapis.com/css2?family=Sorts+Mill+Goudy&family=Open+Sans:wght@600;700&display=swap" rel="stylesheet">
<style>
  :root {
    --backdrop: #5e5e5e;
    --paper: #ffffff;
    --orange: #f47c45;
    --ink-grey: #58595b;
    --dial-context: #b5c9d6;
    --dial-culture: #dddcd4;
    --dial-clout: #6f7275;
    --dial-connection: #ff7f47;
    --on-dial: #ffffff;
  }
  * { margin: 0; padding: 0; box-sizing: border-box; }
  html, body {
    width: 1200px;
    height: 1000px;
    overflow: hidden;
    background: var(--backdrop);
  }
  .canvas {
    position: relative;
    width: 1200px;
    height: 1000px;
    background: var(--backdrop);
  }
  .book-cover {
    position: absolute;
    left: 341px;
    top: 85px;
    width: 519px;
    height: 831px;
    background: var(--paper);
    text-align: center;
  }
  .title {
    position: absolute;
    left: 0;
    right: 0;
    top: 72px;
    font-family: "Sorts Mill Goudy", Georgia, serif;
    font-weight: 400;
    color: var(--orange);
    font-size: 88px;
    line-height: 68px;
    letter-spacing: -1px;
  }
  .title span { display: block; }
  .subtitle {
    position: absolute;
    left: 0;
    right: 0;
    top: 239px;
    font-family: "Sorts Mill Goudy", Georgia, serif;
    color: var(--ink-grey);
    font-size: 26px;
    line-height: 32px;
    letter-spacing: 0.4px;
  }
  .subtitle span { display: block; }
  .pillars {
    position: absolute;
    left: 99px;
    top: 385px;
    width: 324px;
    height: 324px;
  }
  .pillar-letter {
    font-family: "Sorts Mill Goudy", Georgia, serif;
    font-size: 60px;
    fill: var(--on-dial);
  }
  .pillar-label {
    font-family: "Open Sans", Arial, sans-serif;
    font-weight: 600;
    font-size: 13px;
    fill: var(--on-dial);
  }
  .author {
    position: absolute;
    left: 0;
    right: 0;
    top: 744px;
    font-family: "Sorts Mill Goudy", Georgia, serif;
    color: var(--ink-grey);
    font-size: 34px;
    font-variant: small-caps;
    letter-spacing: 1.5px;
  }
</style>
</head>
<body>
<div class="canvas">
  <div class="book-cover">
    <h1 class="title"><span>The 4Cs</span><span>Compass</span></h1>
    <p class="subtitle">
      <span>Practical Bargaining &amp;</span>
      <span>Persuasion Methods</span>
      <span>for Cross-Border Success</span>
    </p>
    <svg class="pillars" viewBox="0 0 324 324" aria-label="The four Cs: Context, Culture, Clout, Connection">
      <circle cx="79" cy="79" r="79" fill="var(--dial-context)"/>
      <circle cx="241" cy="79" r="79" fill="var(--dial-culture)"/>
      <circle cx="79" cy="242" r="79" fill="var(--dial-clout)"/>
      <circle cx="241" cy="242" r="79" fill="var(--dial-connection)"/>
      <g text-anchor="middle">
        <text class="pillar-letter" x="79" y="92">C</text>
        <text class="pillar-label" x="79" y="121">CONTEXT</text>
        <text class="pillar-letter" x="241" y="92">C</text>
        <text class="pillar-label" x="241" y="121">CULTURE</text>
        <text class="pillar-letter" x="79" y="255">C</text>
        <text class="pillar-label" x="79" y="284">CLOUT</text>
        <text class="pillar-letter" x="241" y="255">C</text>
        <text class="pillar-label" x="241" y="284">CONNECTION</text>
      </g>
    </svg>
    <p class="author">Harvel T. Ostrand</p>
  </div>
</div>
</body>
</html>
```